Tolvik Commercial Cleaning is lookong for a new business card design.

A fresh new design that's professional and stylish. We need a serious upgrade to our business cards. I have included pictures of our existing ones. Our clients include professional individuals and business owners. We woupdblike something professional and upbeat. Please have fun and see what you come uo with.

Target Market(s)

Property managers, business owners, facility managers and other similar professionals

Industry/Entity Type

Janitorial

Contact Information for Business Card

Name, cell, office number, email, web address

Font styles to use
Sans Serif

Colors

Designer to choose colors to be used in the design.

Requirements
Must have
• please use the green color in our logo
Nice to have
• Bar code
Should not have
• Address

```html
<!DOCTYPE html>
<html lang="en">
<head>
<meta charset="utf-8">
<title>Tolvik Commercial Cleaning – Business Card</title>
<link rel="stylesheet" href="https://fonts.googleapis.com/css2?family=Poppins:wght@500;600;700&family=Roboto:wght@400&display=swap">
<style>
  :root {
    --bg: #2a2a2a;
    --brand-green: #3ab65a;
    --brand-blue: #2f62a0;
    --paper: #ffffff;
    --ink-light: #ffffff;
  }
  * { box-sizing: border-box; margin: 0; padding: 0; }
  html, body { width: 1200px; height: 947px; overflow: hidden; }
  body {
    background: var(--bg);
    position: relative;
    font-family: "Poppins", sans-serif;
  }
  .card {
    position: absolute;
    top: 319px;
    width: 540px;
    height: 309px;
    border-radius: 22px;
    overflow: hidden;
    box-shadow: 0 14px 30px rgba(0,0,0,0.45);
  }
  /* Front side */
  .card--front {
    left: 30px;
    background: var(--brand-green);
    display: flex;
    align-items: center;
    justify-content: center;
  }
  .card--front .brand-name {
    color: var(--ink-light);
    font-weight: 700;
    font-size: 38px;
    line-height: 1.15;
    text-align: center;
    letter-spacing: -0.5px;
  }
  /* Back side */
  .card--back {
    left: 630px;
    background: var(--paper);
    display: flex;
  }
  .back-brand {
    width: 300px;
    display: flex;
    align-items: center;
    justify-content: center;
  }
  .back-brand .brand-name {
    color: var(--brand-green);
    font-weight: 700;
    font-size: 30px;
    line-height: 1.15;
    text-align: center;
    letter-spacing: -0.4px;
  }
  .divider-band {
    width: 14px;
    background: var(--brand-green);
    position: relative;
  }
  .divider-band .stripes {
    position: absolute;
    top: 18px;
    left: 0;
    width: 14px;
  }
  .contact-panel {
    flex: 1;
    background: var(--brand-blue);
    border-left: 3px solid var(--paper);
    padding: 86px 0 0 30px;
  }
  .contact-panel .person-name {
    color: var(--brand-green);
    font-weight: 600;
    font-size: 23px;
    margin-bottom: 14px;
  }
  .contact-list { list-style: none; }
  .contact-list li {
    display: flex;
    align-items: center;
    gap: 10px;
    color: var(--ink-light);
    font-family: "Roboto", sans-serif;
    font-size: 14.5px;
    line-height: 22px;
  }
  .contact-list svg { width: 13px; height: 13px; flex: none; }
</style>
</head>
<body>

  <section class="card card--front" aria-label="Business card front">
    <p class="brand-name">Tolvik<br>Commercial Cleaning</p>
  </section>

  <section class="card card--back" aria-label="Business card back">
    <div class="back-brand">
      <p class="brand-name">Tolvik<br>Commercial<br>Cleaning</p>
    </div>
    <div class="divider-band">
      <svg class="stripes" viewBox="0 0 14 16" aria-hidden="true">
        <rect x="0" y="0" width="14" height="2" fill="#ffffff"/>
        <rect x="0" y="5" width="14" height="2" fill="#ffffff"/>
        <rect x="0" y="10" width="14" height="2" fill="#ffffff"/>
      </svg>
    </div>
    <div class="contact-panel">
      <p class="person-name">Mara Lindqvist</p>
      <ul class="contact-list">
        <li>
          <svg viewBox="0 0 24 24" aria-hidden="true"><path fill="#3ab65a" d="M6.6 10.8a15 15 0 0 0 6.6 6.6l2.2-2.2c.3-.3.7-.4 1-.2 1.1.4 2.3.6 3.6.6.6 0 1 .4 1 1V20c0 .6-.4 1-1 1A17 17 0 0 1 3 4c0-.6.4-1 1-1h3.5c.6 0 1 .4 1 1 0 1.3.2 2.5.6 3.6.1.3 0 .7-.2 1z"/></svg>
          (555) 014-2290
        </li>
        <li>
          <svg viewBox="0 0 24 24" aria-hidden="true"><rect x="2" y="5" width="20" height="14" rx="2" fill="#3ab65a"/><path d="M3 6l9 7 9-7" fill="none" stroke="#2f62a0" stroke-width="2"/></svg>
          mara@tolvikcleaning.com
        </li>
        <li>
          <svg viewBox="0 0 24 24" aria-hidden="true"><circle cx="12" cy="12" r="10" fill="#3ab65a"/><path d="M2 12h20M12 2c3 3 3 17 0 20M12 2c-3 3-3 17 0 20" fill="none" stroke="#2f62a0" stroke-width="1.5"/></svg>
          www.tolvikcleaning.com
        </li>
      </ul>
    </div>
  </section>

</body>
</html>
```